Flaschenetiketten-Design in rechteckiger Grundform für Biermanufaktur
Zielgruppe
Wir repräsentieren eine Bier-Manufaktur in der Gründungsphase und sind auf der Suche nach einem Designvorschlag für die Flaschenetiketten.
Unsere Zielgruppe sind Liebhaber, die auf der Suche nach dem Speziellen und Lokalen sind. Der Biergenuss abseits des Massenmarktes soll im Entwurf sichtbar/transportiert werden. Die Bier-Manufaktur steht zeitgleich für Trend-Kreationen mit bodenständigem Ursprung.
Aufgabenstellung
Die Herkunft der Gründer Familie aus dem Schweizer Kanton Simplon soll im Vordergrund stehen, hierzu bitte das Familienwappen / einzelne Elemente siehe Dateiupload berücksichtigen.
Das Etikett soll eine rechteckige Grundform haben.
Folgende Angaben sollen sich im Etikett wiederfinden:
- Biersorte: 'Lager' (zukünftig soll es möglich sein, Biersorte auf dem Etikett zu wechseln)
Brand: 'Hearty Kandrom'
'Biermanufaktur Walliser Ursprungs'
Die Schrift soll klar und nicht zu verspielt sein.

```html
<!DOCTYPE html>
<html lang="de">
<head>
<meta charset="utf-8">
<title>Hearty Kandrom – Lagerbier Etikett</title>
<link href="https://fonts.googleapis.com/css2?family=Josefin+Sans:wght@600;700&display=swap" rel="stylesheet">
<style>
  :root {
    --page: #ffffff;
    --label: #2c2c2c;
    --frame-light: #d9d9d9;
    --frame-dark: #6e6e6e;
    --silver-light: #e6e6e6;
    --silver-mid: #a9a9a9;
    --silver-dark: #7b7b7b;
    --text: #ffffff;
  }
  html, body {
    margin: 0;
    padding: 0;
    width: 844px;
    height: 1200px;
    overflow: hidden;
    background: var(--page);
    font-family: "Josefin Sans", sans-serif;
  }
  .canvas {
    position: relative;
    width: 844px;
    height: 1200px;
  }
  .label {
    position: absolute;
    left: 62px;
    top: 200px;
    width: 720px;
    height: 800px;
    box-sizing: border-box;
    padding: 11px;
    background: linear-gradient(90deg, var(--frame-dark), var(--frame-light) 45%, var(--frame-dark) 70%, var(--frame-light));
    box-shadow: 0 8px 16px rgba(0, 0, 0, 0.35);
  }
  .label-inner {
    position: relative;
    width: 100%;
    height: 100%;
    background: var(--label);
    color: var(--text);
    text-align: center;
  }
  .crest {
    position: absolute;
    left: 50%;
    top: 52px;
    width: 266px;
    height: 325px;
    transform: translateX(-50%);
  }
  .beer-type {
    position: absolute;
    left: 0;
    right: 0;
    top: 403px;
    font-size: 28px;
    font-weight: 600;
    letter-spacing: 2px;
  }
  .brand {
    position: absolute;
    left: 0;
    right: 0;
    top: 500px;
    margin: 0;
    font-size: 100px;
    font-weight: 700;
    line-height: 0.98;
    letter-spacing: 3px;
  }
  .tagline {
    position: absolute;
    left: 0;
    right: 0;
    top: 702px;
    font-size: 21px;
    font-weight: 700;
    letter-spacing: 3px;
  }
</style>
</head>
<body>
<div class="canvas">
  <div class="label">
    <div class="label-inner">
      <svg class="crest" viewBox="0 0 266 325" role="img" aria-label="Silbernes Familienwappen der Gründerfamilie">
        <defs>
          <linearGradient id="silver" x1="0" y1="0" x2="1" y2="1">
            <stop offset="0" stop-color="var(--silver-mid)"/>
            <stop offset="0.45" stop-color="var(--silver-light)"/>
            <stop offset="1" stop-color="var(--silver-dark)"/>
          </linearGradient>
        </defs>
        <path d="M2 2 H264 V200 Q264 262 133 323 Q2 262 2 200 Z" fill="url(#silver)"/>
      </svg>
      <div class="beer-type">- LAGERBIER -</div>
      <h1 class="brand">HEARTY<br>KANDROM</h1>
      <div class="tagline">BIERMANUFAKTUR WALLISER URSPRUNGS</div>
    </div>
  </div>
</div>
</body>
</html>
```